Vellisant - Quality health delivered at your door

Vellisant offers home and Community Based Services for adults who wish to continue live independently in their communities. We increase accessibility to health care, reduce health care delivery gap, reduce mortality and morbidity, reduce health while promoting healthy living in the comfort of our patients communities or homes.

We provide on site services and deliver high quality healthcare at your door. Our experienced physicians coordinate care with our certified nurse practitioners and provide chronic care management, physical therapy, rehabilitation and medications management.

Target Market(s)

Older population living in independent living facilities

Industry/Entity Type

Health Care

Contact Information for Business Card

Vellisant

Number of Pages Required

4 page

Font styles to use
Sans Serif

Colors

Designer to choose colors to be used in the design.

```html
<!DOCTYPE html>
<html lang="en">
<head>
<meta charset="utf-8">
<title>Vellisant – Quality health delivered at your door</title>
<link href="https://fonts.googleapis.com/css2?family=Montserrat:wght@400;500;600&family=Open+Sans:wght@400;600&display=swap" rel="stylesheet">
<style>
:root{
  --orange:#f7941d;
  --dark-green:#1f3300;
  --olive:#738a2a;
  --ink:#1c2a0d;
  --text:#444;
  --white:#fff;
  --footer:#2f3a16;
}
*{box-sizing:border-box;margin:0;padding:0}
html,body{width:1200px;height:2449px;overflow:hidden;background:var(--white)}
body{font-family:"Open Sans",Arial,sans-serif;color:var(--text);position:relative}
.heading{font-family:"Montserrat",Arial,sans-serif}
a{color:inherit;text-decoration:none}
.abs{position:absolute}
.btn{position:absolute;display:flex;align-items:center;justify-content:center;border-radius:26px;font-family:"Montserrat",sans-serif;font-weight:500;color:var(--white);font-size:17px;text-transform:uppercase}
.btn-orange{background:var(--orange)}
.btn-dark{background:var(--dark-green)}

/* header */
.brand{left:68px;top:10px;width:130px;text-align:center}
.brand-mark{width:62px;height:62px;border-radius:50%;background:var(--dark-green);margin:0 auto 6px;border:4px solid var(--orange)}
.brand-name{font-family:"Montserrat",sans-serif;font-weight:500;font-size:19px;color:var(--ink);letter-spacing:.5px}
.join-top{left:779px;top:15px;width:344px;height:44px;font-size:19px;font-weight:400}
.top-links{left:489px;top:77px;font-family:"Montserrat",sans-serif;font-size:15px;color:#111;letter-spacing:.5px}
.top-contact{left:783px;top:77px;display:flex;gap:26px;font-size:15px;align-items:center}
.top-contact span{display:flex;align-items:center;gap:9px}
.top-contact .mail{font-style:italic;color:#666}
.top-contact .phone{font-weight:600;color:#555}

.main-nav{left:0;top:114px;width:1200px;height:56px;background:var(--dark-green);display:flex;align-items:center;justify-content:center;gap:21px;color:var(--white);font-family:"Montserrat",sans-serif;font-size:15.5px}

/* hero */
.hero{left:0;top:170px;width:1200px;height:508px;background:linear-gradient(90deg,#f1f1ef 0%,#eeeeea 40%,#ddd8cc 62%,#c9c2b2 80%,#e9e6e0 100%)}
.hero h1{position:absolute;left:79px;top:112px;font-family:"Montserrat",sans-serif;font-weight:400;font-size:48px;line-height:62px;color:var(--ink)}
.hero p{position:absolute;left:79px;top:248px;width:520px;font-size:20px;line-height:33px;color:#555}
.learn{left:77px;top:336px;width:166px;height:52px}
.join-hero{left:269px;top:336px;width:152px;height:52px}

/* stay home */
.video{left:77px;top:730px;width:421px;height:312px;background:linear-gradient(120deg,#d9e4e2,#ece7e2 50%,#cbbfb0)}
.video-bar{position:absolute;left:5px;right:5px;bottom:5px;height:26px;background:#1e1e1e;display:flex;align-items:center;gap:10px;padding:0 10px}
.video-bar .track{flex:1;height:4px;background:#555;position:relative}
.video-bar .track i{position:absolute;left:0;top:0;width:20%;height:4px;background:#c21717}
.video-bar b{width:8px;height:10px;border-left:3px solid #fff;border-right:3px solid #fff}
.stay{left:553px;top:728px;width:570px}
.stay h2{font-family:"Montserrat",sans-serif;font-weight:400;font-size:37px;color:#111;letter-spacing:1px;margin-bottom:24px}
.stay p{font-size:15.5px;line-height:25px;color:#444;margin-bottom:25px}
.read{left:552px;top:990px;width:175px;height:50px}

/* services */
.services{left:0;top:1094px;width:1200px;height:980px;background:var(--olive);color:var(--white)}
.services h2{position:absolute;top:52px;width:100%;text-align:center;font-family:"Montserrat",sans-serif;font-weight:400;font-size:37px;letter-spacing:1px}
.svc{position:absolute;width:260px;text-align:center}
.svc svg{display:block;margin:0 auto;height:84px}
.svc h3{font-family:"Montserrat",sans-serif;font-weight:400;font-size:18.5px;line-height:23px;margin-top:26px;height:46px}
.svc p{font-size:13.5px;line-height:23px;margin-top:6px}
.view{left:513px;top:877px;width:175px;height:51px}

/* footer */
.footer{left:0;top:2074px;width:1200px;height:313px;background:linear-gradient(90deg,#3e4a1f 0%,#2a3312 45%,#3b4521 70%,#2b3313 100%)}
.footer h4{position:absolute;font-family:"Montserrat",sans-serif;font-weight:400;font-size:24px;color:var(--white)}
.footer h4 em{font-style:normal;color:var(--orange)}
.footer h4::after{content:"";position:absolute;left:0;top:42px;width:48px;height:3px;background:var(--orange)}
.about-text{position:absolute;left:78px;top:106px;width:330px;font-size:14px;line-height:23px;color:var(--white)}
.contact-row{position:absolute;left:432px;display:flex;align-items:center;gap:17px;color:var(--white);font-size:14.5px;line-height:23px}
.contact-row .ring{width:42px;height:42px;border:2px solid var(--white);border-radius:50%;display:flex;align-items:center;justify-content:center;flex-shrink:0}
.f-brand{position:absolute;left:860px;top:68px;width:200px;text-align:center}
.f-brand .mark{width:74px;height:74px;border-radius:50%;background:#8b8b83;border:3px solid #ddd;margin:0 auto 10px}
.f-brand .name{font-family:"Montserrat",sans-serif;font-size:21px;color:var(--white);letter-spacing:.5px}
.socials{position:absolute;left:867px;top:200px;display:flex;gap:7px}
.socials span{width:40px;height:40px;border-radius:50%}
.bottom{left:0;top:2387px;width:1200px;height:62px;background:var(--orange);display:flex;align-items:center;justify-content:space-between;padding:0 78px;font-family:"Montserrat",sans-serif;font-size:14px;color:var(--white)}
.bottom nav{display:flex;gap:41px}
</style>
</head>
<body>

<header>
  <div class="abs brand"><div class="brand-mark"></div><div class="brand-name">VELLISANT</div></div>
  <a class="btn btn-orange join-top">Join Our Community Now</a>
  <div class="abs top-links">HOME &nbsp;/&nbsp; ABOUT &nbsp;/&nbsp; CONTACT</div>
  <div class="abs top-contact">
    <span class="mail"><svg width="18" height="13" viewBox="0 0 18 13"><rect width="18" height="13" fill="#6a8f2a"/><path d="M0 0l9 7 9-7" stroke="#fff" stroke-width="1.5" fill="none"/></svg>info@vellisant.com</span>
    <span class="phone"><svg width="16" height="16" viewBox="0 0 24 24"><path fill="#6a8f2a" d="M6.6 10.8a15 15 0 006.6 6.6l2.2-2.2a1 1 0 011-.25 11.4 11.4 0 003.6.57 1 1 0 011 1V20a1 1 0 01-1 1A17 17 0 013 4a1 1 0 011-1h3.5a1 1 0 011 1c0 1.25.2 2.45.57 3.57a1 1 0 01-.25 1z"/></svg>123-456-7890</span>
  </div>
  <nav class="abs main-nav">
    <a>Assisted Living</a><a>Skilled Nursing</a><a>Independent Living</a><a>Home &amp; Community Based Living</a><a>Respite Care</a><a>Rehabilitation</a><a>Cognify Learning</a>
  </nav>
</header>

<section class="abs hero" role="img" aria-label="Photo of a smiling senior couple sitting together at home">
  <h1>Live Independently in<br>Your Communities</h1>
  <p>Lorem Ipsum is simply dummy text of the printing and typesetting industry. Lorem Ipsum has been the</p>
  <a class="btn btn-dark learn">Learn More</a>
  <a class="btn btn-orange join-hero">Join Now</a>
</section>

<div class="abs video" role="img" aria-label="Video still of a caregiver with a smiling senior woman">
  <div class="video-bar"><b></b><div class="track"><i></i></div></div>
</div>
<section class="abs stay">
  <h2>STAY HOME</h2>
  <p>Vellisant offers home and Community Based Services for adults who wish to continue to live independently in the comfort of their communities.</p>
  <p>We provide on site services and deliver high quality healthcare at your door. Our experienced physicians coordinate care with our certified nurse practitioners and provide chronic care management, physical therapy, rehabilitation and medications management.</p>
</section>
<a class="btn btn-orange read">Read More &raquo;</a>

<section class="abs services">
  <h2>SERVICES</h2>

  <div class="svc" style="left:71px;top:135px">
    <svg viewBox="0 0 84 84"><rect x="8" y="20" width="68" height="56" rx="4" fill="#fff"/><rect x="30" y="10" width="24" height="12" rx="3" fill="none" stroke="#fff" stroke-width="4"/><circle cx="42" cy="46" r="15" fill="#738a2a"/><path d="M37 36h10v5h5v10h-5v5H37v-5h-5V41h5z" fill="#fff"/></svg>
    <h3>Comprehensive primary<br>Care Services</h3>
    <p>Lorem Ipsum is simply dummy text of the printing and typesetting industry.</p>
  </div>
  <div class="svc" style="left:337px;top:135px">
    <svg viewBox="0 0 84 84"><circle cx="52" cy="28" r="22" fill="none" stroke="#fff" stroke-width="3"/><path d="M47 16h10v7h7v10h-7v7H47v-7h-7V23h7z" fill="#fff"/><circle cx="30" cy="46" r="12" fill="#fff"/><path d="M8 82c0-14 10-22 22-22s22 8 22 22z" fill="#fff"/></svg>
    <h3>Coordination of Specialty<br>Care</h3>
    <p>Lorem Ipsum is simply dummy text of the printing and typesetting industry.</p>
  </div>
  <div class="svc" style="left:602px;top:135px">
    <svg viewBox="0 0 84 84"><circle cx="42" cy="12" r="9" fill="#fff"/><rect x="34" y="22" width="16" height="26" rx="4" fill="#fff"/><rect x="8" y="48" width="68" height="8" fill="#fff"/><path d="M16 56l-6 24M68 56l6 24M30 56l-4 14M54 56l4 14" stroke="#fff" stroke-width="4"/></svg>
    <h3>Chronic Disease<br>Management</h3>
    <p>Lorem Ipsum is simply dummy text of the printing and typesetting industry.</p>
  </div>
  <div class="svc" style="left:868px;top:135px">
    <svg viewBox="0 0 84 84"><circle cx="24" cy="10" r="8" fill="#fff"/><rect x="17" y="20" width="14" height="30" rx="4" fill="#fff"/><path d="M20 50v30M28 50v30" stroke="#fff" stroke-width="5"/><circle cx="56" cy="30" r="7" fill="#fff"/><circle cx="56" cy="64" r="14" fill="none" stroke="#fff" stroke-width="4"/><rect x="50" y="38" width="12" height="20" rx="3" fill="#fff"/></svg>
    <h3>Transitional Care</h3>
    <p>Lorem Ipsum is simply dummy text of the printing and typesetting industry.</p>
  </div>

  <div class="svc" style="left:71px;top:400px">
    <svg viewBox="0 0 84 84"><rect x="30" y="2" width="24" height="12" rx="2" fill="#fff"/><circle cx="42" cy="28" r="14" fill="#fff"/><path d="M16 82c0-22 10-32 26-32s26 10 26 32z" fill="#fff"/><path d="M38 58h8v6h6v8h-6v6h-8v-6h-6v-8h6z" fill="#738a2a"/></svg>
    <h3>Skilled Nursing</h3>
    <p>Lorem Ipsum is simply dummy text of the printing and typesetting industry.</p>
  </div>
  <div class="svc" style="left:337px;top:400px">
    <svg viewBox="0 0 84 84"><circle cx="26" cy="20" r="9" fill="#fff"/><rect x="16" y="31" width="20" height="30" rx="5" fill="#fff"/><path d="M20 60v22M32 60v22" stroke="#fff" stroke-width="5"/><circle cx="58" cy="16" r="9" fill="#fff"/><path d="M46 70l4-42h16l4 42z" fill="#fff"/><path d="M54 70v12M62 70v12" stroke="#fff" stroke-width="4"/></svg>
    <h3>Social Services<br>Assessment</h3>
    <p>Lorem Ipsum is simply dummy text of the printing and typesetting industry.</p>
  </div>
  <div class="svc" style="left:602px;top:400px">
    <svg viewBox="0 0 84 84"><path d="M8 38L42 8l34 30" stroke="#fff" stroke-width="5" fill="none"/><path d="M42 58c-10-8-16-13-16-20a8 8 0 0116-2 8 8 0 0116 2c0 7-6 12-16 20z" fill="#fff"/><path d="M10 50l14 24h14M74 50L60 74H46" stroke="#fff" stroke-width="5" fill="none"/></svg>
    <h3>Home Health<br>Assistance</h3>
    <p>Lorem Ipsum is simply dummy text of the printing and typesetting industry.</p>
  </div>
  <div class="svc" style="left:868px;top:400px">
    <svg viewBox="0 0 84 84"><circle cx="50" cy="12" r="9" fill="#fff"/><path d="M40 24l-16 20h10l12-10z" fill="#fff"/><circle cx="20" cy="48" r="7" fill="#fff"/><rect x="6" y="54" width="72" height="10" rx="4" fill="#fff"/><rect x="4" y="68" width="76" height="6" fill="#fff"/></svg>
    <h3>Physical Therapy</h3>
    <p>Lorem Ipsum is simply dummy text of the printing and typesetting industry.</p>
  </div>

  <div class="svc" style="left:205px;top:670px">
    <svg viewBox="0 0 84 84"><path d="M20 80V62C8 54 6 40 10 28 16 10 36 4 52 8c16 4 24 18 22 32-1 6 4 10 4 14l-8 2v10c0 4-4 6-8 6h-6v8z" fill="#fff"/><path d="M28 26c6-6 16-6 22 0M32 40c6 4 14 4 20 0" stroke="#738a2a" stroke-width="3" fill="none"/></svg>
    <h3>Mental Health</h3>
    <p>Lorem Ipsum is simply dummy text of the printing and typesetting industry.</p>
  </div>
  <div class="svc" style="left:469px;top:670px">
    <svg viewBox="0 0 84 84"><path d="M10 40c4 14 14 20 30 20h30l6-8H40c-10 0-14-6-18-14z" fill="#fff"/><path d="M34 60v16M20 78h34" stroke="#fff" stroke-width="5"/><path d="M46 6l16 16" stroke="#fff" stroke-width="6"/><circle cx="64" cy="10" r="5" fill="#fff"/></svg>
    <h3>Dental Health</h3>
    <p>Lorem Ipsum is simply dummy text of the printing and typesetting industry.</p>
  </div>
  <div class="svc" style="left:734px;top:670px">
    <svg viewBox="0 0 120 84"><path d="M6 20h80c10 0 20 12 26 26v20H6z" fill="#fff"/><rect x="14" y="28" width="20" height="14" fill="#738a2a"/><rect x="40" y="28" width="20" height="14" fill="#738a2a"/><path d="M68 28h16l12 14H68z" fill="#738a2a"/><circle cx="28" cy="68" r="9" fill="#fff" stroke="#738a2a" stroke-width="4"/><circle cx="90" cy="68" r="9" fill="#fff" stroke="#738a2a" stroke-width="4"/></svg>
    <h3>Transportation</h3>
    <p>Lorem Ipsum is simply dummy text of the printing and typesetting industry.</p>
  </div>

  <a class="btn btn-orange view">View All &raquo;</a>
</section>

<footer class="abs footer" role="img" aria-label="Dimmed photo of a caregiver with a senior, tinted dark olive">
  <h4 style="left:78px;top:42px"><em>ABOUT</em> VELLISANT</h4>
  <p class="about-text">Lorem Ipsum is simply dummy text of the printing and typesetting industry. Lorem Ipsum has been the industry's standard dummy text ever since the 1500s, when an unknown printer took a galley of type and scrambled it to make a type specimen book.</p>
  <h4 style="left:436px;top:42px"><em>CONTACT</em> VELLISANT</h4>
  <div class="contact-row" style="top:108px"><span class="ring"><svg width="14" height="20" viewBox="0 0 14 20"><path d="M7 0a7 7 0 00-7 7c0 5 7 13 7 13s7-8 7-13a7 7 0 00-7-7z" fill="#fff"/><circle cx="7" cy="7" r="2.5" fill="#2a3312"/></svg></span><span>123 Building Name, Street Name, City,<br>Country - Zipcode</span></div>
  <div class="contact-row" style="top:166px"><span class="ring"><svg width="18" height="18" viewBox="0 0 24 24"><path fill="#fff" d="M6.6 10.8a15 15 0 006.6 6.6l2.2-2.2a1 1 0 011-.25 11.4 11.4 0 003.6.57 1 1 0 011 1V20a1 1 0 01-1 1A17 17 0 013 4a1 1 0 011-1h3.5a1 1 0 011 1c0 1.25.2 2.45.57 3.57a1 1 0 01-.25 1z"/></svg></span><span style="font-size:16px">123-456-7890</span></div>
  <div class="contact-row" style="top:226px"><span class="ring"><svg width="18" height="13" viewBox="0 0 18 13"><rect width="18" height="13" fill="#fff"/><path d="M0 0l9 7 9-7" stroke="#2a3312" stroke-width="1.5" fill="none"/></svg></span><span style="font-style:italic">info@vellisant.com</span></div>
  <div class="f-brand"><div class="mark"></div><div class="name">VELLISANT</div></div>
  <div class="socials"><span style="background:#3b5998"></span><span style="background:#1da1f2"></span><span style="background:#dd4b39"></span><span style="background:#0e76a8"></span></div>
</footer>

<div class="abs bottom">
  <span>© VELLISANT - 2017. All Rights Reserved.</span>
  <nav><a>HOME</a><a>ABOUT</a><a>PRIVACY POLICY</a><a>TERMS &amp; CONDITIONS</a><a>CONTACT</a></nav>
</div>

</body>
</html>
```